KBT Business Cards

We require business cards for our business. We would like a matte black back to the card, with our logo centred in the middle. The front side of the card is open to design.

Target Market(s)

Clients looking for legal services (professional)

Industry/Entity Type

Legal

Contact Information for Business Card

Doran Kelbrath
Partner
Mobile: 0461 738 524
Email: doran@kbtlaw.co
Website: www.kbtlaw.co
Level 3, 118 Wendmore Street
Sydney NSW 2000

Font styles to use
Other font styles liked:
• Avenir

Colors
f04a50
ffffff
1b1b1b

Requirements
Must have
• Black back with logo included in the centre of the card.
• Our font is Avenir.

```html
<!DOCTYPE html>
<html lang="en">
<head>
<meta charset="UTF-8">
<title>KBT Legal Business Cards</title>
<link href="https://fonts.googleapis.com/css2?family=Nunito+Sans:wght@400;600;800&family=Oswald:wght@500&display=swap" rel="stylesheet">
<style>
  :root {
    --stage: #111111;
    --card: #1b1b1b;
    --accent: #d81f4f;
    --ink: #ffffff;
    --ink-soft: #e8e8e8;
  }
  * { margin: 0; padding: 0; box-sizing: border-box; }
  html, body {
    width: 1200px; height: 900px; overflow: hidden;
    background: var(--stage);
  }
  .sheet {
    width: 1200px; height: 900px;
    display: flex; flex-direction: column; align-items: center; justify-content: center;
    gap: 34px;
  }
  .card {
    width: 700px; height: 400px;
    background: var(--card);
    position: relative;
    box-shadow: 0 10px 30px rgba(0,0,0,0.6);
    font-family: "Nunito Sans", "Avenir", sans-serif;
    color: var(--ink);
  }
  /* Back: centred name mark */
  .card--back { display: flex; align-items: center; justify-content: center; }
  .brand { display: flex; align-items: center; gap: 22px; }
  .brand__square { width: 70px; height: 70px; background: var(--accent); }
  .brand__name {
    font-weight: 800; font-size: 40px; line-height: 1.05;
    letter-spacing: 1px; color: var(--ink); text-transform: uppercase;
  }
  /* Front: contact details */
  .card--front { padding: 0 60px; }
  .details {
    position: absolute; top: 150px; left: 60px; right: 40px;
    display: flex; align-items: center;
  }
  .person { text-align: right; width: 280px; }
  .person__name {
    font-family: "Oswald", "Arial Narrow", sans-serif;
    font-weight: 500; font-size: 40px; line-height: 1;
    color: var(--accent); text-transform: uppercase; letter-spacing: 0.5px;
  }
  .person__role { font-size: 20px; color: var(--ink-soft); margin-top: 6px; }
  .divider { width: 2px; height: 76px; background: var(--accent); margin: 0 22px; }
  .contact { list-style: none; font-size: 18px; line-height: 1.45; color: var(--ink-soft); }
  .contact li { display: flex; align-items: center; gap: 10px; }
  .contact svg { width: 13px; height: 13px; flex: none; }
  .address {
    position: absolute; left: 0; right: 0; bottom: 52px;
    text-align: center; font-size: 19px; color: var(--ink-soft);
  }
</style>
</head>
<body>
<main class="sheet">
  <section class="card card--back" aria-label="Card back">
    <div class="brand">
      <span class="brand__square"></span>
      <span class="brand__name">KBT Legal</span>
    </div>
  </section>

  <section class="card card--front" aria-label="Card front">
    <div class="details">
      <div class="person">
        <h1 class="person__name">Doran Kelbrath</h1>
        <p class="person__role">General Manager</p>
      </div>
      <span class="divider"></span>
      <ul class="contact">
        <li>
          <svg viewBox="0 0 16 16" aria-hidden="true"><path d="M4 1l3 3-2 2c1 2 3 4 5 5l2-2 3 3-2 2C7 14 2 9 2 3z" fill="none" stroke="var(--accent)" stroke-width="1.6"/></svg>
          0461 738 524
        </li>
        <li>
          <svg viewBox="0 0 16 16" aria-hidden="true"><rect x="1.5" y="3.5" width="13" height="9" fill="none" stroke="var(--accent)" stroke-width="1.4"/><path d="M1.5 4l6.5 5 6.5-5" fill="none" stroke="var(--accent)" stroke-width="1.4"/></svg>
          doran@kbtlaw.co
        </li>
        <li>
          <svg viewBox="0 0 16 16" aria-hidden="true"><circle cx="8" cy="8" r="6.5" fill="none" stroke="var(--accent)" stroke-width="1.3"/><ellipse cx="8" cy="8" rx="3" ry="6.5" fill="none" stroke="var(--accent)" stroke-width="1.1"/><path d="M1.5 8h13" stroke="var(--accent)" stroke-width="1.1"/></svg>
          www.kbtlaw.co
        </li>
      </ul>
    </div>
    <p class="address">Level 3, 118 Wendmore Street, Sydney NSW 2000</p>
  </section>
</main>
</body>
</html>
```